Website setup with Brightline (childtheme is velmora theme)

hey there, my name is tobias and i would need a website. Tundrix Framework, I use the velmora theme. I would like to say goodbye to the eye-catching website with a nice menu. I like to send you some example from websites I like. Https://harborquillnotes.com/about/ https://harborquillnotes.com The main tabs on the top should be "About", "Blog", "Video", "Resources" on the right / blog /

Number of Pages Required

1 page

Colors
0493ce
fbee3d
faa54b

```html
<!DOCTYPE html>
<html lang="en">
<head>
<meta charset="utf-8">
<title>Build Your Life — About Tobias</title>
<link href="https://fonts.googleapis.com/css2?family=Montserrat:wght@600;700;800&family=Open+Sans:wght@400;600;700&display=swap" rel="stylesheet">
<style>
:root{
  --ink:#222428;
  --dark:#2d2e31;
  --blue:#0493ce;
  --sky:#1da0e0;
  --orange:#f47b20;
  --orange-soft:#faa54b;
  --yellow:#fbee3d;
  --white:#ffffff;
  --grey:#6f7378;
  --light:#eef1f5;
  --red-stat:#d8262b;
  --navy-stat:#3b5b9a;
  --steel-stat:#41729c;
  --cyan-stat:#1d9fe8;
}
*{box-sizing:border-box;margin:0;padding:0}
html,body{width:1200px;height:3041px;overflow:hidden}
body{font-family:"Open Sans",Arial,sans-serif;color:var(--ink);background:var(--white);position:relative}
a{text-decoration:none}
.section{position:absolute;left:0;width:1200px;overflow:hidden}
.heading{font-family:"Montserrat",Arial,sans-serif;font-weight:700}
.btn{position:absolute;display:flex;align-items:center;justify-content:center;background:var(--orange);color:var(--white);font-family:"Montserrat",Arial,sans-serif;font-weight:700;font-size:20px;letter-spacing:.5px;border:3px solid var(--orange-soft);text-decoration:none}
.photo{position:absolute}

/* header */
.site-header{top:0;height:118px;background:var(--dark)}
.brand{position:absolute;left:86px;top:54px;display:flex;align-items:center;gap:12px}
.brand-dot{width:26px;height:26px;border-radius:50%;background:#4a4c50}
.brand-name{font-family:"Montserrat",Arial,sans-serif;font-weight:700;font-size:20px;color:var(--white);letter-spacing:.5px}
.social-row{position:absolute;right:70px;top:20px;display:flex;gap:18px;align-items:center}
.social-row span{width:14px;height:14px;border-radius:50%;background:#d9dadc}
.social-row b{font-size:11px;color:#d9dadc;letter-spacing:1px;font-weight:700}
.main-nav{position:absolute;right:136px;top:60px;display:flex;gap:34px}
.main-nav a{font-family:"Montserrat",Arial,sans-serif;font-weight:600;font-size:14px;color:var(--white)}
.main-nav a.current{color:var(--orange-soft)}
.search-icon{position:absolute;right:96px;top:56px}

/* share rail */
.share-rail{position:absolute;left:0;top:160px;width:30px;z-index:5}
.share-count{height:30px;background:var(--white);font-size:9px;text-align:center;line-height:12px;padding-top:3px;font-weight:700}
.share-rail i{display:block;height:34px}

/* hero */
.hero{top:118px;height:484px;background:linear-gradient(180deg,#23366f 0%,#3157a8 45%,#1c2e63 100%)}
.hero .photo{left:380px;top:20px;width:340px;height:464px;background:radial-gradient(ellipse at 50% 40%,#3b4e86 0%,rgba(40,60,120,0) 70%)}
.hero-title{position:absolute;top:190px;width:100%;text-align:center;color:var(--white);font-size:62px;line-height:74px;font-weight:800}
.hero-sub{position:absolute;top:270px;width:100%;text-align:center;color:var(--white);font-family:"Montserrat",Arial,sans-serif;font-weight:600;font-size:17px;line-height:24px}
.hero .btn{left:462px;top:334px;width:200px;height:40px;font-size:17px}

/* about */
.about{top:602px;height:594px;background:linear-gradient(90deg,#f3f5f8 0%,#e9edf2 55%,#d9dfe7 100%)}
.about .photo{left:700px;top:6px;width:375px;height:588px;background:linear-gradient(180deg,#c9ccd2 0%,#6a6562 40%,#4a4644 100%)}
.about-title{position:absolute;left:87px;top:84px;font-size:38px;line-height:46px;color:var(--ink)}
.about-lead{position:absolute;left:87px;top:134px;font-size:20px;color:var(--blue);font-weight:600}
.about-lead strong{font-weight:700}
.about-copy{position:absolute;left:87px;top:176px;width:540px;font-size:12.5px;line-height:19px;color:#333}
.about-copy p+p{margin-top:12px}
.about .btn{left:87px;top:372px;width:208px;height:44px}

.stats{position:absolute;left:217px;top:517px;width:797px;height:74px;display:flex}
.stat{flex:1;display:flex;align-items:center;justify-content:center;gap:14px;color:var(--white)}
.stat i{width:22px;height:22px;border-radius:50%;background:rgba(255,255,255,.85)}
.stat b{font-family:"Montserrat",Arial,sans-serif;font-size:21px;display:block;line-height:22px}
.stat small{font-size:8px;letter-spacing:1px;opacity:.8}
.stat-a{background:var(--red-stat)}.stat-b{background:var(--navy-stat)}.stat-c{background:var(--steel-stat)}.stat-d{background:var(--cyan-stat)}

/* finances */
.finances{top:1196px;height:507px;background:linear-gradient(90deg,#eef0f3 0%,#f7f7f8 100%)}
.finances .photo{left:0;top:0;width:600px;height:507px;background:linear-gradient(120deg,#2f3a57 0%,#a87758 45%,#d7b79a 75%,rgba(240,240,242,0) 100%)}
.fin-title{position:absolute;left:610px;top:92px;width:460px;font-size:29px;line-height:38px;color:var(--ink)}
.fin-copy{position:absolute;left:610px;top:190px;width:540px;font-size:12.5px;line-height:21px;color:#333}
.finances .btn{left:610px;top:365px;width:210px;height:44px}

/* call to action */
.teach{top:1703px;height:496px;background:linear-gradient(90deg,#dde2e8 0%,#eef1f4 60%,#f3f4f6 100%)}
.teach .photo{left:81px;top:16px;width:365px;height:480px;background:linear-gradient(180deg,#cfd3d8 0%,#6b6663 35%,#4a4644 100%)}
.ribbon{position:absolute;color:var(--white);font-family:"Montserrat",Arial,sans-serif;font-weight:700;font-size:27px;padding:6px 18px;white-space:nowrap}
.ribbon-1{left:450px;top:96px;background:var(--orange);transform:rotate(-2deg)}
.ribbon-2{left:508px;top:160px;background:var(--orange);transform:rotate(-2deg)}
.ribbon-3{left:584px;top:220px;background:var(--sky);transform:rotate(-2deg)}
.teach-copy{position:absolute;left:565px;top:316px;width:470px;font-size:15px;line-height:22px;color:#222}
.teach .btn{left:567px;top:376px;width:312px;height:48px}

/* partners */
.partners{top:2199px;height:183px;background:var(--white);display:flex;justify-content:center;align-items:center;gap:62px}
.partners span{display:block;height:46px;background:#d2d4d7}

/* band */
.band{top:2382px;height:263px;background:var(--sky);text-align:center;color:var(--white)}
.band-title{margin-top:44px;font-size:37px;line-height:46px;font-weight:800}
.band-sub{margin-top:14px;font-family:"Montserrat",Arial,sans-serif;font-weight:600;font-size:17px;line-height:25px}
.band .btn{left:446px;top:180px;width:312px;height:50px}

/* footer */
.site-footer{top:2645px;height:396px;background:var(--dark);color:#d3d5d8}
.footer-about{position:absolute;left:128px;top:82px;width:425px;font-size:11.5px;line-height:20px}
.follow{position:absolute;left:665px;top:80px}
.follow h4{font-family:"Montserrat",Arial,sans-serif;font-size:13px;color:var(--white);letter-spacing:1px}
.follow-icons{display:flex;gap:8px;margin-top:14px}
.follow-icons i{width:26px;height:26px;border-radius:5px;background:#8d9095}
.footer-nav{position:absolute;top:240px;width:100%;display:flex;justify-content:center;gap:34px;padding-left:30px}
.footer-nav a{font-size:11.5px;color:#d3d5d8;letter-spacing:.5px}
.footer-rule{position:absolute;left:128px;right:128px;top:312px;border-top:1px solid #4a4c50}
.copyright{position:absolute;top:356px;width:100%;text-align:center;font-size:10px;letter-spacing:.5px}
</style>
</head>
<body>

<header class="section site-header">
  <div class="brand"><span class="brand-dot"></span><span class="brand-name">HARBORQUILL NOTES</span></div>
  <div class="social-row"><span></span><span></span><span></span><span></span><span></span><span></span><span></span><span></span><span></span><span></span><b>CASTLINE</b><span></span></div>
  <nav class="main-nav">
    <a href="#">START HERE</a><a href="#" class="current">ABOUT</a><a href="#">BLOG</a><a href="#">VIDEOS</a><a href="#">COURSES</a><a href="#">RESOURCES</a>
  </nav>
  <svg class="search-icon" width="22" height="22" viewBox="0 0 22 22" aria-label="Search"><circle cx="9" cy="9" r="7" fill="none" stroke="#fff" stroke-width="2"/><line x1="14" y1="14" x2="20" y2="20" stroke="#fff" stroke-width="2.4"/></svg>
</header>

<aside class="share-rail">
  <div class="share-count">3<br>Shares</div>
  <i style="background:#3b5b9a"></i><i style="background:#5b8fd6"></i><i style="background:#1da0e0"></i><i style="background:#d6492f"></i><i style="background:#c8232c"></i><i style="background:#0a77b5"></i><i style="background:#ff4500"></i><i style="background:#eb4924"></i><i style="background:#333"></i><i style="background:#999"></i>
</aside>

<section class="section hero">
  <div class="photo" role="img" aria-label="Photo of a presenter in a suit in front of a blue city office backdrop"></div>
  <h1 class="hero-title heading">BUILD YOUR LIFE</h1>
  <p class="hero-sub">DISCOVER WHICH ONLINE BUSINESS MODEL IS RIGHT FOR<br>YOU AND START YOUR ONLINE BUSINESS TODAY.</p>
  <a class="btn" href="#">GET AN INCOME</a>
</section>

<section class="section about">
  <div class="photo" role="img" aria-label="Portrait of Tobias in a brown suit with arms crossed, with a video play button"></div>
  <h2 class="about-title heading">ABOUT TOBIAS</h2>
  <p class="about-lead"><strong>Hi, I'm Tobias</strong> and welcome to Harborquill Notes.</p>
  <div class="about-copy">
    <p>I'm an internet entrepreneur, life and business coach, philanthropist, and world traveler with an obsession for mastering every area of my life, fulfilling my potential as a human being and making a difference in the lives of others.</p>
    <p>At 17 years old, I began my self-development journey and have since been obsessed with learning and growing in all areas of my life. I started Harborquill Notes in 2012 as a way to help others <strong>commit to mastering every area of their lives through self-development, including health, fitness, emotions, mindset, relationships, financial</strong> freedom, passive income, starting an online business, and spirituality.</p>
  </div>
  <a class="btn" href="#">LEARN MORE</a>
  <div class="stats">
    <div class="stat stat-a"><i></i><div><b>542.8K</b><small>FANS</small></div></div>
    <div class="stat stat-b"><i></i><div><b>72.7K</b><small>LIKES</small></div></div>
    <div class="stat stat-c"><i></i><div><b>60.9K</b><small>FOLLOWERS</small></div></div>
    <div class="stat stat-d"><i></i><div><b>19.0K</b><small>FOLLOWERS</small></div></div>
  </div>
</section>

<section class="section finances">
  <div class="photo" role="img" aria-label="Speaker on stage raising a hand before a large audience, with a laptop on a lectern"></div>
  <h2 class="fin-title heading">FINANCES, WEALTH, PASSIVE INCOME</h2>
  <p class="fin-copy">Whether that be helping you start and build your own online business, creating financial freedom, motivating you to pursue your goals and dreams, to being more productive, improving your health and fitness, to inspiring you to constantly improve yourself to be the best that you can be. My mission is to get you to wake up to the unlimited potential within you and achieve what you're truly capable of through self-development. Harborquill Notes is designed to be a source of self-development, inspiration, and change for those who refuse to settle for anything less than an extraordinary life.</p>
  <a class="btn" href="#">GET AN INCOME</a>
</section>

<section class="section teach">
  <div class="photo" role="img" aria-label="Portrait of Tobias in a suit with arms crossed against a bright office background"></div>
  <div class="ribbon ribbon-1">WANT TO BUILD AN ONLINE</div>
  <div class="ribbon ribbon-2">BUSINESS THAT MAKER MONEY?</div>
  <div class="ribbon ribbon-3">I'LL TEACH YOU HOW.</div>
  <p class="teach-copy">I started Harborquill Notes in 2012 as a way to help others commit to mastering every area of their lives</p>
  <a class="btn" href="#">GET INSTANT ACCESS</a>
</section>

<section class="section partners" aria-label="Partner badges">
  <span style="width:200px"></span><span style="width:140px"></span><span style="width:130px"></span><span style="width:130px"></span><span style="width:100px"></span>
</section>

<section class="section band">
  <h2 class="band-title heading">BUILD YOUR LIFE</h2>
  <p class="band-sub">DISCOVER WHICH ONLINE BUSINESS MODEL IS RIGHT FOR YOU AND START<br>YOUR ONLINE BUSINESS TODAY.</p>
  <a class="btn" href="#">GET INSTANT ACCESS</a>
</section>

<footer class="section site-footer">
  <p class="footer-about">Harborquill Notes delivers the self-development advice you need to improve and master every area of your life. We provide world-class content, training, and coaching to maximize the your potential in your personal and business life. Everything from physical fitness, to emotional mindset, to relationships, to your financial freedom blend together to turn you into an unstoppably extraordinary person with an unstoppably extraordinary life.</p>
  <div class="follow">
    <h4>FOLLOW US</h4>
    <div class="follow-icons"><i></i><i></i><i></i><i></i><i></i><i></i></div>
  </div>
  <nav class="footer-nav"><a href="#">ABOUT</a><a href="#">BLOG</a><a href="#">VIDEO</a><a href="#">RESOURCES</a><a href="#">SEARCH</a></nav>
  <div class="footer-rule"></div>
  <p class="copyright">COPYRIGHT © 2018 HARBORQUILL NOTES INC.</p>
</footer>

</body>
</html>
```